Sophisticated, clean website reflecting my feminine, playful side to sell my abstract art,

I need a website no more than 3 pages to showcase my paintings, a little about me and some contact info. I do abstracts so looking for something a little edgy, yet feminine and current.
Updates

Hi there, These are some artists websites that I Iike: Marnelvoss.com (I like how airy it is) peterwallombry.com garethpolvens.com (I like how it scrolls) I'll need a place for a photo ( a headshot-i do not have it yet so I'll need to be able to upload that later) as well as an area for my bio. Also, it's important that I will be able to upload any new photos and descriptions easily so it should be user friendly. Lastly, I like in a sunny place so would like to have this seem upbeat and playful as that is how i like to paint. thanks-I'm trying to upload my photos now -

Target Market(s)

ppl ages 35-70 who want large scale art for their homes

Industry/Entity Type

art

Coding

Coded - Design and coding required

Number of Pages Required

3 page

Colors

Designer to choose colors to be used in the design.

Requirements
Must have
• photos of my art, a place for my bio, be easy to reach me. tasteful-nothing too "in your face" -my clients are pretty high end and organized. They like clean lines
Nice to have
• sophisticated background, muted tones in the back-similar clean font throughout-no cursive
Should not have
• too many dark areas. Too many blocks of color. Too serious.

```html
<!DOCTYPE html>
<html lang="en">
<head>
<meta charset="utf-8">
<title>Painting Abstract Art Lumen</title>
<link rel="stylesheet" href="https://fonts.googleapis.com/css2?family=Marcellus&family=Poppins:wght@400;500&display=swap">
<style>
  :root {
    --ink: #1c1c1c;
    --paper: #ffffff;
    --cream: #f9f8f5;
    --field: #f3efe8;
    --tan: #b8966f;
    --tan-soft: #cfc3a8;
    --olive: #b7ab84;
    --muted: #8a7a66;
    --frame: #f07d12;
    --frame-dark: #c9600a;
    --hero-a: #ead9bb;
    --hero-b: #dcc6a0;
  }
  * { box-sizing: border-box; margin: 0; padding: 0; }
  html, body { width: 1200px; height: 2866px; overflow: hidden; }
  body { position: relative; background: var(--paper); color: var(--ink); font-family: "Poppins", sans-serif; }
  .abs { position: absolute; }
  .serif { font-family: "Marcellus", serif; }
  .btn { position: absolute; background: var(--ink); color: #fff; font-size: 14px; display: flex; align-items: center; justify-content: center; }

  /* header */
  .site-header { position: absolute; left: 0; top: 0; width: 1200px; height: 60px; background: var(--cream); z-index: 3; }
  .brand { position: absolute; left: 60px; top: 18px; display: flex; align-items: center; gap: 10px; font-family: "Marcellus", serif; font-size: 20px; color: var(--ink); }
  .brand-square { width: 22px; height: 22px; background: var(--tan); }
  .nav a { position: absolute; top: 20px; font-size: 14px; color: var(--ink); text-decoration: none; }

  /* hero */
  .hero { position: absolute; left: 0; top: 60px; width: 1200px; height: 525px; background: linear-gradient(135deg, var(--hero-a), var(--hero-b) 60%, var(--hero-a)); }
  .hero-title { position: absolute; left: 60px; top: 235px; font-size: 47px; line-height: 1.1; }
  .hero-sub { position: absolute; left: 61px; top: 300px; width: 460px; font-size: 14px; line-height: 22px; color: var(--muted); }

  .frame { position: absolute; border: 16px solid var(--frame); box-shadow: inset 0 0 0 2px var(--frame-dark), 0 2px 0 var(--frame-dark); }

  /* about */
  .about { position: absolute; left: 0; top: 585px; width: 1200px; height: 575px; background: var(--cream); }
  .eyebrow { font-size: 14px; color: var(--tan); }
  .about-text { position: absolute; left: 618px; top: 763px; width: 520px; font-size: 14px; line-height: 22.5px; }

  /* gallery */
  .card { position: absolute; width: 252px; height: 238px; background: #fff; box-shadow: 0 0 6px rgba(0,0,0,.12); padding: 8px; }
  .card .art { width: 100%; height: 100%; }
  .card-name { position: absolute; width: 252px; text-align: center; font-family: "Marcellus", serif; font-size: 17px; }
  .card-price { position: absolute; width: 252px; text-align: center; font-size: 14px; color: var(--tan); font-weight: 500; }

  /* contact */
  .contact { position: absolute; left: 600px; top: 2117px; width: 600px; height: 450px; background: var(--cream); }
  .field { position: absolute; left: 638px; width: 465px; height: 37px; background: var(--field); }
  .field .ico { position: absolute; left: 0; top: 0; width: 38px; height: 37px; background: var(--tan); display: flex; align-items: center; justify-content: center; }
  .field span { position: absolute; left: 49px; top: 9px; font-size: 14px; }

  /* footer */
  .site-footer { position: absolute; left: 0; top: 2567px; width: 1200px; height: 263px; background: var(--ink); color: #fff; }
  .foot-head { position: absolute; top: 2617px; font-family: "Marcellus", serif; font-size: 17px; color: var(--tan); }
  .foot-text { position: absolute; font-size: 14px; line-height: 20px; color: #fff; }
  .social { position: absolute; top: 2667px; width: 38px; height: 38px; background: var(--tan-soft); }
  .copyright { position: absolute; left: 0; top: 2830px; width: 1200px; height: 36px; background: var(--olive); color: #fff; font-size: 12px; display: flex; align-items: center; justify-content: center; }
</style>
</head>
<body>

<header class="site-header">
  <div class="brand"><span class="brand-square"></span>Art Lumen</div>
  <nav class="nav">
    <a style="left:765px">My Paintings</a>
    <a style="left:886px">About Me</a>
    <a style="left:986px">Contact</a>
  </nav>
  <svg class="abs" style="left:1076px;top:20px" width="22" height="20" viewBox="0 0 22 20" fill="none" stroke="#1c1c1c" stroke-width="1.6"><path d="M1 2h3l3 11h11l2-8H6"/><circle cx="9" cy="17" r="1.4"/><circle cx="16" cy="17" r="1.4"/></svg>
  <svg class="abs" style="left:1120px;top:20px" width="20" height="20" viewBox="0 0 20 20" fill="none" stroke="#1c1c1c" stroke-width="2"><circle cx="8" cy="8" r="6"/><path d="M12.5 12.5L18 18"/></svg>
</header>

<section class="hero" role="img" aria-label="Light woven bamboo texture background"></section>
<h1 class="hero-title serif">Painting Abstract Art Lumen</h1>
<p class="hero-sub">Lorem Ipsum is simply dummy text of the printing and typesetting industry.</p>
<div class="btn" style="left:60px;top:407px;width:112px;height:37px">Contact US</div>

<svg class="abs" style="left:780px;top:160px" width="250" height="90" viewBox="0 0 250 90" fill="none" stroke="#6b6256" stroke-width="1.3"><path d="M133 9L20 58M133 9L235 80"/><circle cx="133" cy="9" r="5" fill="#cfc7bb"/></svg>
<div class="frame" style="left:661px;top:232px;width:445px;height:300px;transform:rotate(4deg)">
  <div role="img" aria-label="Abstract painting in ochre, navy and rust tones" style="width:100%;height:100%;background:radial-gradient(circle at 45% 50%,#1f4a6a 0,#c9971e 30%,#d9b44a 55%,#ece6da 80%)"></div>
</div>

<section class="about"></section>
<svg class="abs" style="left:160px;top:655px" width="250" height="90" viewBox="0 0 250 90" fill="none" stroke="#6b6256" stroke-width="1.3"><path d="M116 11L10 84M116 11L236 57"/><circle cx="116" cy="11" r="5" fill="#cfc7bb"/></svg>
<div class="frame" style="left:74px;top:728px;width:468px;height:323px;transform:rotate(-4deg)">
  <div role="img" aria-label="Photo of the artist painting at an easel in her studio" style="width:100%;height:100%;background:linear-gradient(120deg,#8d8f90,#c7c6c2 45%,#6f6e6a)"></div>
</div>
<p class="eyebrow abs" style="left:619px;top:681px">About Me</p>
<h2 class="serif abs" style="left:618px;top:704px;font-size:31px;font-weight:400">Welcome To Painting Abstract Art Lumen</h2>
<p class="about-text">Lorem Ipsum is simply dummy text of the printing and typesetting industry. Lorem Ipsum has been the industry's standard dummy text ever since the 1500s, when an unknown printer took a galley of type and scrambled it to make a type specimen book. It has survived not only five centuries, but also the leap into electronic typesetting, remaining essentially unchanged. It was popularised in the 1960s with the release of Letraset sheets containing Lorem Ipsum passages,and more recently with desktop publishing software like Aldus PageMaker including versions of Lorem Ipsum.</p>
<div class="btn" style="left:617px;top:978px;width:105px;height:37px">Read More</div>

<p class="eyebrow abs" style="left:0;width:1200px;text-align:center;top:1240px">My Paintings</p>
<h2 class="serif abs" style="left:0;width:1200px;text-align:center;top:1264px;font-size:33px;font-weight:400">Explore The Abstract Art Lumen</h2>

<div class="card" style="left:60px;top:1329px"><div class="art" role="img" aria-label="Abstract rose painting in mauve and deep brown" style="background:linear-gradient(135deg,#efe8e6,#b58a86 50%,#5a2d2e)"></div></div>
<div class="card" style="left:336px;top:1329px"><div class="art" role="img" aria-label="Abstract swirl painting in gold and blue" style="background:linear-gradient(135deg,#e8e1c9,#c9a23a 45%,#2f5f8a)"></div></div>
<div class="card" style="left:612px;top:1329px"><div class="art" role="img" aria-label="Abstract red spiral painting on white" style="background:radial-gradient(circle at 60% 40%,#a33b22,#d59a88 35%,#f3efec 70%)"></div></div>
<div class="card" style="left:888px;top:1329px"><div class="art" role="img" aria-label="Abstract floral painting in violet and blue" style="background:linear-gradient(135deg,#d9d0de,#7a5a9a 50%,#3b3566)"></div></div>

<div class="card-name" style="left:60px;top:1576px">Painting Name</div><div class="card-price" style="left:60px;top:1601px">$500</div>
<div class="card-name" style="left:336px;top:1576px">Painting Name</div><div class="card-price" style="left:336px;top:1601px">$500</div>
<div class="card-name" style="left:612px;top:1576px">Painting Name</div><div class="card-price" style="left:612px;top:1601px">$500</div>
<div class="card-name" style="left:888px;top:1576px">Painting Name</div><div class="card-price" style="left:888px;top:1601px">$500</div>

<div class="card" style="left:60px;top:1653px"><div class="art" role="img" aria-label="Abstract painting with teal drips on cream" style="background:linear-gradient(90deg,#e8e2d6,#8fc0cf 45%,#dfe6e4)"></div></div>
<div class="card" style="left:336px;top:1653px"><div class="art" role="img" aria-label="Abstract rose painting in mauve and deep brown" style="background:linear-gradient(135deg,#efe8e6,#b58a86 50%,#5a2d2e)"></div></div>
<div class="card" style="left:612px;top:1653px"><div class="art" role="img" aria-label="Abstract painting in greens and teal" style="background:linear-gradient(135deg,#d6e8c8,#3f9a55 50%,#1d5a4a)"></div></div>
<div class="card" style="left:888px;top:1653px"><div class="art" role="img" aria-label="Abstract floral painting in violet and navy" style="background:radial-gradient(circle at 55% 50%,#3a3460,#8a6aa6 40%,#e2d9dc 80%)"></div></div>

<div class="card-name" style="left:60px;top:1899px">Painting Name</div><div class="card-price" style="left:60px;top:1924px">$500</div>
<div class="card-name" style="left:336px;top:1899px">Painting Name</div><div class="card-price" style="left:336px;top:1924px">$500</div>
<div class="card-name" style="left:612px;top:1899px">Painting Name</div><div class="card-price" style="left:612px;top:1924px">$500</div>
<div class="card-name" style="left:888px;top:1899px">Painting Name</div><div class="card-price" style="left:888px;top:1924px">$500</div>

<div class="btn" style="left:546px;top:1996px;width:108px;height:37px">View More</div>

<div class="abs" role="img" aria-label="Close-up of an abstract painting in purple, violet and black" style="left:0;top:2117px;width:600px;height:450px;background:radial-gradient(circle at 55% 50%,#3a2a55,#7a5aa6 35%,#c7b3d6 65%,#e9e2e4)"></div>
<section class="contact"></section>
<h2 class="serif abs" style="left:642px;top:2150px;font-size:31px;font-weight:400">Get In Touch</h2>

<div class="field" style="top:2208px"><div class="ico"><svg width="18" height="20" viewBox="0 0 18 20" fill="none" stroke="#fff" stroke-width="1.4"><circle cx="9" cy="6" r="4"/><path d="M1 19c0-5 4-7 8-7s8 2 8 7z"/></svg></div><span>Name*</span></div>
<div class="field" style="top:2256px"><div class="ico"><svg width="18" height="18" viewBox="0 0 18 18" fill="none" stroke="#fff" stroke-width="1.4"><path d="M4 1l3 4-2 2c1 2 3 4 5 5l2-2 4 3-2 3C8 16 2 10 1 4z"/></svg></div><span>Phone No.*</span></div>
<div class="field" style="top:2306px"><div class="ico"><svg width="22" height="16" viewBox="0 0 22 16" fill="none" stroke="#fff" stroke-width="1.4"><rect x="1" y="1" width="20" height="14"/><path d="M1 1l10 8 10-8M1 15l7-7M21 15l-7-7"/></svg></div><span>E-mail*</span></div>
<div class="field" style="top:2355px;height:105px"><div class="ico"><svg width="20" height="20" viewBox="0 0 20 20" fill="none" stroke="#fff" stroke-width="1.4"><path d="M10 1a9 8 0 1 1-4 15l-5 3 2-5A9 8 0 0 1 10 1z"/></svg></div><span>Comment*</span></div>
<div class="btn" style="left:638px;top:2492px;width:87px;height:37px">Submit</div>

<footer class="site-footer"></footer>
<div class="abs serif" style="left:60px;top:2628px;display:flex;align-items:center;gap:10px;font-size:24px;color:var(--tan)"><span style="width:22px;height:22px;background:var(--tan)"></span>Art Lumen</div>
<p class="foot-text" style="left:61px;top:2710px;width:250px">Lorem Ipsum is simply dummy text of the printing and typesetting industry. Lorem Ipsum</p>

<h3 class="foot-head" style="left:340px;font-weight:400">Quick Links</h3>
<p class="foot-text" style="left:340px;top:2660px">My Paintings</p>
<p class="foot-text" style="left:340px;top:2698px">About Me</p>
<p class="foot-text" style="left:340px;top:2736px">Contact</p>

<h3 class="foot-head" style="left:614px;font-weight:400">Contact Us</h3>
<svg class="abs" style="left:614px;top:2662px" width="14" height="18" viewBox="0 0 14 18" fill="none" stroke="#fff" stroke-width="1.3"><path d="M7 17s6-6 6-10A6 6 0 0 0 1 7c0 4 6 10 6 10z"/><circle cx="7" cy="7" r="2"/></svg>
<p class="foot-text" style="left:642px;top:2656px;width:190px">123,Lorem Ipsum is simply dummy text</p>
<svg class="abs" style="left:613px;top:2712px" width="18" height="18" viewBox="0 0 18 18" fill="none" stroke="#fff" stroke-width="1.3"><path d="M4 1l3 4-2 2c1 2 3 4 5 5l2-2 4 3-2 3C8 16 2 10 1 4z"/></svg>
<p class="foot-text" style="left:642px;top:2710px;font-weight:500">(123) 456 7890</p>
<svg class="abs" style="left:613px;top:2753px" width="20" height="14" viewBox="0 0 20 14" fill="none" stroke="#fff" stroke-width="1.3"><rect x="1" y="1" width="18" height="12"/><path d="M1 1l9 7 9-7"/></svg>
<p class="foot-text" style="left:642px;top:2750px">Info@abstractartlumen.com</p>

<h3 class="foot-head" style="left:889px;font-weight:400">Social Links</h3>
<div class="social" style="left:888px" aria-label="Social link one"></div>
<div class="social" style="left:949px" aria-label="Social link two"></div>
<div class="social" style="left:1008px" aria-label="Social link three"></div>
<div class="social" style="left:1068px" aria-label="Social link four"></div>

<div class="copyright">Copyright 2022, painting abstract art Lumen. All Rights Reserved.</div>

</body>
</html>
```